Business card design for Automotive workshop

We need a business card for a new automotive repair and tyre shop called Keelstone Prime Automotive located in New Zealand. We are a clean, modern and fresh workshop and company.

Front needs to feature logo,
my name:
Marlo Fenwicke (director)

Address:
48 Tarn Lane
Whitianga 3510

Phone: 07 594 2713
Mobile: 027 451 9362
Email: office@keelstoneautomotive.example.nz
Website: keelstoneautomotive.example.nz

Back needs to feature an area to write down appointment details, date and time.

Also feature a list of jobs and work we do such as,
Vehicle Servicing
All Mechanical Repairs
Warrant of Fitness
Tyres & Wheel Alignments
Automotive Diagnostics
Automotive Parts & Supplies

```html
<!DOCTYPE html>
<html lang="en">
<head>
<meta charset="utf-8">
<title>Keelstone Prime Automotive – Business Card</title>
<link href="https://fonts.googleapis.com/css2?family=Open+Sans:ital,wght@0,400;0,600;0,700;1,700&display=swap" rel="stylesheet">
<style>
  :root {
    --bg: #e7e5e3;
    --card: #141414;
    --panel: #333333;
    --red: #e3202a;
    --white: #ffffff;
    --rule: #bdbdbd;
  }
  html, body {
    margin: 0;
    padding: 0;
    width: 1200px;
    height: 794px;
    overflow: hidden;
    background: var(--bg);
    font-family: "Open Sans", Arial, sans-serif;
  }
  .canvas {
    width: 1200px;
    height: 794px;
    display: flex;
    align-items: center;
    justify-content: center;
    gap: 40px;
  }
  .card {
    position: relative;
    width: 540px;
    height: 300px;
    background: var(--card);
    color: var(--white);
    box-shadow: 0 6px 18px rgba(0,0,0,0.25);
    overflow: hidden;
  }

  /* Back side */
  .appointment-title {
    position: absolute;
    top: 22px;
    left: 0;
    right: 0;
    text-align: center;
    color: var(--red);
    font-weight: 700;
    font-style: italic;
    font-size: 19px;
    margin: 0;
  }
  .appointment-panel {
    position: absolute;
    top: 54px;
    left: 40px;
    right: 40px;
    height: 112px;
    background: var(--panel);
  }
  .appointment-field {
    position: absolute;
    left: 40px;
    right: 40px;
    display: flex;
    align-items: baseline;
    gap: 8px;
    font-weight: 700;
    font-style: italic;
    font-size: 13px;
  }
  .appointment-field .write-line {
    flex: 1;
    border-bottom: 1px dashed var(--rule);
    transform: translateY(-3px);
  }
  .field-date { top: 72px; }
  .field-time { top: 124px; padding-left: 170px; }

  .works-heading {
    position: absolute;
    top: 184px;
    left: 0;
    right: 0;
    display: flex;
    align-items: center;
    justify-content: center;
    gap: 12px;
    font-weight: 700;
    font-style: italic;
    font-size: 13px;
  }
  .works-heading .accent-line {
    width: 70px;
    height: 1.5px;
    background: var(--red);
  }
  .works-list {
    position: absolute;
    top: 214px;
    left: 20px;
    right: 20px;
    margin: 0;
    padding: 0;
    list-style: none;
    display: flex;
    flex-wrap: wrap;
    justify-content: center;
    column-gap: 14px;
    row-gap: 8px;
    font-size: 11.5px;
  }
  .works-list li::before {
    content: "";
    display: inline-block;
    width: 5px;
    height: 5px;
    border-radius: 50%;
    background: var(--red);
    margin-right: 5px;
    vertical-align: middle;
    transform: translateY(-2px);
  }

  /* Front side */
  .brand {
    position: absolute;
    top: 54px;
    right: 34px;
    display: flex;
    align-items: center;
    gap: 10px;
  }
  .brand-mark {
    width: 14px;
    height: 14px;
    background: var(--red);
  }
  .brand-name {
    font-weight: 700;
    font-size: 21px;
    color: var(--white);
    letter-spacing: 0.5px;
  }
  .person {
    position: absolute;
    top: 148px;
    left: 30px;
    width: 205px;
    text-align: right;
  }
  .person-name {
    margin: 0;
    color: var(--red);
    font-weight: 700;
    font-size: 20px;
  }
  .person-role {
    margin: 2px 0 0;
    font-size: 12px;
  }
  .divider {
    position: absolute;
    top: 146px;
    left: 250px;
    width: 1px;
    height: 80px;
    background: var(--rule);
  }
  .contacts {
    position: absolute;
    top: 146px;
    left: 266px;
    margin: 0;
    padding: 0;
    list-style: none;
    font-size: 12px;
    line-height: 20px;
  }
  .contacts li {
    display: flex;
    align-items: center;
    gap: 8px;
  }
  .contacts svg {
    width: 11px;
    height: 11px;
    fill: var(--red);
    flex: none;
  }
  .address {
    position: absolute;
    top: 246px;
    left: 30px;
    margin: 0;
    font-size: 12.5px;
    font-style: normal;
  }
</style>
</head>
<body>
<main class="canvas">

  <section class="card card-back" aria-label="Card back">
    <h2 class="appointment-title">Appointment Details</h2>
    <div class="appointment-panel"></div>
    <div class="appointment-field field-date"><span>Date</span><span class="write-line"></span></div>
    <div class="appointment-field field-time"><span>Time</span><span class="write-line"></span></div>
    <div class="works-heading"><span class="accent-line"></span><span>Our Works</span><span class="accent-line"></span></div>
    <ul class="works-list">
      <li>Vehicle Servicing</li>
      <li>Warrant of Fitness</li>
      <li>Automotive Parts &amp; Supplies</li>
      <li>Automotive Diagnostics</li>
      <li>Tyres &amp; Wheel Alignments</li>
      <li>All Mechanical Repairs</li>
    </ul>
  </section>

  <section class="card card-front" aria-label="Card front">
    <div class="brand">
      <span class="brand-mark"></span>
      <span class="brand-name">Keelstone Prime Automotive</span>
    </div>

    <div class="person">
      <h1 class="person-name">Marlo Fenwicke</h1>
      <p class="person-role">Director</p>
    </div>

    <span class="divider"></span>

    <ul class="contacts">
      <li>
        <svg viewBox="0 0 24 24" aria-hidden="true"><path d="M6.6 10.8a15.1 15.1 0 0 0 6.6 6.6l2.2-2.2c.3-.3.7-.4 1-.2 1.1.4 2.3.6 3.6.6.6 0 1 .4 1 1V20c0 .6-.4 1-1 1A17 17 0 0 1 3 4c0-.6.4-1 1-1h3.5c.6 0 1 .4 1 1 0 1.3.2 2.5.6 3.6.1.3 0 .7-.2 1z"/></svg>
        <span>07 594 2713</span>
      </li>
      <li>
        <svg viewBox="0 0 24 24" aria-hidden="true"><path d="M7 1h10a2 2 0 0 1 2 2v18a2 2 0 0 1-2 2H7a2 2 0 0 1-2-2V3a2 2 0 0 1 2-2zm0 3v14h10V4zm5 15.5a1 1 0 1 0 0 2 1 1 0 0 0 0-2z"/></svg>
        <span>027 451 9362</span>
      </li>
      <li>
        <svg viewBox="0 0 24 24" aria-hidden="true"><path d="M2 5h20v14H2zm2 2v.5l8 5 8-5V7zm0 2.8V17h16V9.8l-8 5z"/></svg>
        <span>office@keelstoneautomotive.example.nz</span>
      </li>
      <li>
        <svg viewBox="0 0 24 24" aria-hidden="true"><path d="M12 2a10 10 0 1 0 0 20 10 10 0 0 0 0-20zm6.9 6h-3a15 15 0 0 0-1.3-3.9A8 8 0 0 1 18.9 8zM12 4c.8 1.2 1.5 2.5 1.9 4h-3.8c.4-1.5 1.1-2.8 1.9-4zM4.3 14a8 8 0 0 1 0-4h3.4a16 16 0 0 0 0 4zm.8 2h3a15 15 0 0 0 1.3 3.9A8 8 0 0 1 5.1 16zm3-8h-3a8 8 0 0 1 4.3-3.9A15 15 0 0 0 8.1 8zM12 20c-.8-1.2-1.5-2.5-1.9-4h3.8c-.4 1.5-1.1 2.8-1.9 4zm2.3-6H9.7a14 14 0 0 1 0-4h4.6a14 14 0 0 1 0 4zm.3 5.9a15 15 0 0 0 1.3-3.9h3a8 8 0 0 1-4.3 3.9zm1.7-5.9a16 16 0 0 0 0-4h3.4a8 8 0 0 1 0 4z"/></svg>
        <span>keelstoneautomotive.example.nz</span>
      </li>
    </ul>

    <address class="address">48 Tarn Lane Whitianga 3510</address>
  </section>

</main>
</body>
</html>
```